Copper lark buildworks

Copper lark buildworks is a small construction company.
Who is a licenced builder, Carpenter, joiner,
working on heritage ,new build, speacial projects and sometimes furniture

Industry/Entity Type

Construction

```html
<!DOCTYPE html>
<html lang="en">
<head>
<meta charset="utf-8">
<title>Copper lark buildworks – Business Card</title>
<link rel="stylesheet" href="https://fonts.googleapis.com/css2?family=Arvo&family=PT+Sans&display=swap">
<style>
  :root {
    --backdrop: #333333;
    --card-white: #ffffff;
    --brand-green: #13a800;
    --ink-dark: #2b2b2b;
    --rule-grey: #8a8a8a;
  }
  html, body {
    margin: 0;
    padding: 0;
    width: 1200px;
    height: 900px;
    overflow: hidden;
    background: var(--backdrop);
  }
  .canvas {
    position: relative;
    width: 1200px;
    height: 900px;
    background: var(--backdrop);
  }
  .card {
    position: absolute;
    top: 306px;
    width: 439px;
    height: 271px;
    border-radius: 11px;
    overflow: hidden;
  }
  .card--front { left: 149px; background: var(--card-white); }
  .card--back  { left: 608px; background: var(--brand-green); }

  .brand {
    position: absolute;
    left: 0;
    top: 0;
    width: 239px;
    height: 271px;
    display: flex;
    flex-direction: column;
    align-items: center;
    justify-content: center;
    gap: 14px;
    padding-top: 8px;
    box-sizing: border-box;
  }
  .brand__square {
    width: 30px;
    height: 30px;
    background: var(--brand-green);
  }
  .brand__name {
    font-family: "Arvo", serif;
    font-size: 17px;
    color: var(--ink-dark);
    white-space: nowrap;
  }

  .divider {
    position: absolute;
    left: 238px;
    top: 66px;
    width: 1px;
    height: 140px;
    background: var(--rule-grey);
  }

  .contact {
    position: absolute;
    left: 256px;
    top: 58px;
    color: var(--ink-dark);
    font-family: "PT Sans", sans-serif;
  }
  .contact__name {
    font-family: "Arvo", serif;
    font-size: 19px;
    line-height: 1;
    margin: 0;
    white-space: nowrap;
  }
  .contact__first { color: var(--brand-green); }
  .contact__role {
    font-size: 12.5px;
    margin: 6px 0 8px;
  }
  .contact__list {
    list-style: none;
    margin: 0;
    padding: 0;
    font-size: 12.5px;
    line-height: 16.5px;
  }
  .contact__list li {
    display: flex;
    align-items: center;
    gap: 5px;
  }
  .contact__icon {
    width: 10px;
    height: 10px;
    fill: var(--brand-green);
    flex: none;
  }
  .contact__address {
    font-size: 12.5px;
    line-height: 16.5px;
    margin: 6px 0 0;
    font-style: normal;
  }

  .back-brand {
    position: absolute;
    left: 0;
    top: 0;
    width: 100%;
    height: 100%;
    display: flex;
    align-items: center;
    justify-content: center;
    padding-top: 10px;
    box-sizing: border-box;
    font-family: "Arvo", serif;
    font-size: 19px;
    color: var(--card-white);
  }
</style>
</head>
<body>
<main class="canvas">
  <section class="card card--front" aria-label="Business card front">
    <div class="brand">
      <span class="brand__square"></span>
      <span class="brand__name">Copper lark buildworks</span>
    </div>
    <div class="divider"></div>
    <div class="contact">
      <h1 class="contact__name"><span class="contact__first">Harold</span> Penwick</h1>
      <p class="contact__role">Managing Director</p>
      <ul class="contact__list">
        <li>
          <svg class="contact__icon" viewBox="0 0 10 10"><path d="M1 3.5C1 2 2.5 1 5 1s4 1 4 2.5L7.5 4.2 6.8 3H3.2L2.5 4.2zM2 5h6l1 4H1z"/></svg>
          044-555 210 347
        </li>
        <li>
          <svg class="contact__icon" viewBox="0 0 10 10"><path d="M3 0h4a1 1 0 0 1 1 1v8a1 1 0 0 1-1 1H3a1 1 0 0 1-1-1V1a1 1 0 0 1 1-1zm0 1.5v6h4v-6zM5 8.2a.5.5 0 1 0 0 1 .5.5 0 0 0 0-1z"/></svg>
          044-555 210 348
        </li>
        <li>
          <svg class="contact__icon" viewBox="0 0 10 10"><path d="M0 2h10v.8L5 6 0 2.8zM0 3.8l5 3.2 5-3.2V8H0z"/></svg>
          hello@copperlark.com
        </li>
        <li>
          <svg class="contact__icon" viewBox="0 0 10 10"><circle cx="5" cy="5" r="4.6"/><path d="M0.6 5h8.8M5 0.4c-2 2.5-2 6.7 0 9.2M5 0.4c2 2.5 2 6.7 0 9.2" stroke="#fff" stroke-width="0.7" fill="none"/></svg>
          www.copperlark.com
        </li>
      </ul>
      <address class="contact__address">27 Millrace Lane, Westford<br>Easthaven, 402190.</address>
    </div>
  </section>

  <section class="card card--back" aria-label="Business card back">
    <div class="back-brand">Copper lark buildworks</div>
  </section>
</main>
</body>
</html>
```